Business card design for Brivo Engineering Tandem

We need a new business card design along with all the necessary to place an order. The company is Brivo Engineering Tandem and we recently updated our logo.

```html
<!DOCTYPE html>
<html lang="en">
<head>
<meta charset="utf-8">
<title>Brivo Engineering Tandem – Business Card</title>
<link href="https://fonts.googleapis.com/css2?family=Roboto:wght@400;500&display=swap" rel="stylesheet">
<style>
  :root {
    --bg: #2a2a2a;
    --card: #ffffff;
    --ink: #3a3a3a;
    --grey: #8f8f8f;
    --yellow: #e2bd22;
  }
  * { margin: 0; padding: 0; box-sizing: border-box; }
  html, body {
    width: 1200px; height: 1125px; overflow: hidden;
    background: var(--bg);
    font-family: "Roboto", Arial, sans-serif;
  }
  .sheet {
    width: 1200px; height: 1125px;
    display: flex; flex-direction: column; align-items: center; justify-content: center;
    gap: 40px;
  }
  .card {
    position: relative;
    width: 880px; height: 503px;
    background: var(--card);
    border-radius: 56px;
    overflow: hidden;
    box-shadow: 0 8px 24px rgba(0,0,0,.45);
  }
  .brand-band {
    position: absolute; top: 0; bottom: 0;
  }
  .card--front .brand-band { right: 0; width: 180px; }
  .card--back .brand-band { left: 0; width: 236px; }
  .brand-band svg { display: block; width: 100%; height: 100%; }

  .wordmark {
    position: absolute; left: 120px; top: 50%; transform: translateY(-50%);
    display: flex; align-items: center; gap: 16px;
    white-space: nowrap;
  }
  .wordmark__square { width: 24px; height: 24px; background: var(--yellow); flex: none; }
  .wordmark__name {
    font-weight: 500; font-size: 38px; color: var(--grey); letter-spacing: .3px;
  }

  .contact {
    position: absolute; right: 88px; top: 100px;
    text-align: right; color: var(--ink);
  }
  .contact__name { font-size: 38px; font-weight: 500; line-height: 1.1; }
  .contact__role {
    font-size: 15px; letter-spacing: 8px; margin-top: 6px; margin-right: -8px;
  }
  .contact__list { list-style: none; margin-top: 36px; margin-right: -42px; }
  .contact__item {
    display: flex; justify-content: flex-end; align-items: flex-start; gap: 22px;
    font-size: 21px; line-height: 32px; white-space: nowrap;
  }
  .contact__item--address { margin-bottom: 22px; }
  .icon { width: 20px; height: 20px; flex: none; margin-top: 6px; fill: var(--yellow); }
</style>
</head>
<body>
<main class="sheet">

  <section class="card card--front" aria-label="Card front">
    <div class="wordmark">
      <span class="wordmark__square"></span>
      <span class="wordmark__name">Brivo Engineering Tandem</span>
    </div>
    <div class="brand-band" role="img" aria-label="Brand mark decoration in yellow and grey">
      <svg viewBox="0 0 180 503" preserveAspectRatio="none">
        <defs>
          <linearGradient id="bandFront" x1="0" y1="0" x2="0" y2="1">
            <stop offset="0" stop-color="#e2bd22"/>
            <stop offset="1" stop-color="#8f8f8f"/>
          </linearGradient>
        </defs>
        <rect width="180" height="503" fill="url(#bandFront)"/>
      </svg>
    </div>
  </section>

  <section class="card card--back" aria-label="Card back">
    <div class="brand-band" role="img" aria-label="Brand mark decoration in yellow and grey">
      <svg viewBox="0 0 236 503" preserveAspectRatio="none">
        <defs>
          <linearGradient id="bandBack" x1="0" y1="0" x2="0" y2="1">
            <stop offset="0" stop-color="#e2bd22"/>
            <stop offset="1" stop-color="#8f8f8f"/>
          </linearGradient>
        </defs>
        <rect width="236" height="503" fill="url(#bandBack)"/>
      </svg>
    </div>

    <div class="contact">
      <h1 class="contact__name">Helen Marlow</h1>
      <p class="contact__role">DIRECTOR</p>
      <ul class="contact__list">
        <li class="contact__item contact__item--address">
          <span>Brivo Engineering Tandem<br>22b Fernbrook Way, Kettering NN15 4RT</span>
          <svg class="icon" viewBox="0 0 20 20"><path d="M10 1a6 6 0 0 0-6 6c0 4.5 6 12 6 12s6-7.5 6-12a6 6 0 0 0-6-6zm0 8.5A2.5 2.5 0 1 1 10 4.5a2.5 2.5 0 0 1 0 5z"/></svg>
        </li>
        <li class="contact__item">
          <span>01536 482907</span>
          <svg class="icon" viewBox="0 0 20 20"><path d="M2 6c0-2 3-3 8-3s8 1 8 3v2h-4V6.5C13 6 11.5 6 10 6s-3 0-4 .5V8H2zm3 3h10l2 8H3z"/></svg>
        </li>
        <li class="contact__item">
          <span>sales@brivoengineering.co.uk</span>
          <svg class="icon" viewBox="0 0 20 20"><path d="M2 4h16v12H2zm1.5 1.5L10 11l6.5-5.5z"/></svg>
        </li>
        <li class="contact__item">
          <span>www.brivoengineering.co.uk</span>
          <svg class="icon" viewBox="0 0 20 20"><path d="M10 1a9 9 0 1 0 0 18 9 9 0 0 0 0-18zm0 2a7 7 0 0 1 6.9 6H13a11 11 0 0 0-2-5.9A7 7 0 0 1 10 3zM3.1 11H7a11 11 0 0 0 2 5.9A7 7 0 0 1 3.1 11zm0-2A7 7 0 0 1 9 3.1 11 11 0 0 0 7 9zM9 11h2a9 9 0 0 1-1 4.5A9 9 0 0 1 9 11zm0-2a9 9 0 0 1 1-4.5A9 9 0 0 1 11 9zm2 7.9A11 11 0 0 0 13 11h3.9A7 7 0 0 1 11 16.9z"/></svg>
        </li>
      </ul>
    </div>
  </section>

</main>
</body>
</html>
```